Veldmark Supplies Business Card

Professional business card that stand out to our potential customers. Front and back with clean modern design

Industry/Entity Type

Oil and gas

Contact Information for Business Card

Name, address, website , office phone and cell number

Requirements
Must have
• Editable files for each employee

```html
<!DOCTYPE html>
<html lang="en">
<head>
<meta charset="UTF-8">
<title>Veldmark Supplies Business Card</title>
<link href="https://fonts.googleapis.com/css2?family=Montserrat:wght@500;600;800&display=swap" rel="stylesheet">
<style>
  :root {
    --brand-red: #ec2227;
    --brand-blue: #0bb0d3;
    --paper: #ffffff;
    --ink: #1d1d1f;
    --backdrop: #3a3836;
  }
  * { margin: 0; padding: 0; box-sizing: border-box; }
  html, body {
    width: 1200px; height: 900px; overflow: hidden;
    background: var(--backdrop);
    font-family: "Montserrat", sans-serif;
  }
  .sheet {
    position: relative; width: 1200px; height: 900px;
    display: flex; flex-direction: column; align-items: center;
    justify-content: center; gap: 40px;
  }
  .card {
    position: relative; width: 700px; height: 400px;
    border-radius: 28px; overflow: hidden;
    box-shadow: 0 12px 30px rgba(0,0,0,0.45);
  }
  /* Front */
  .card--front {
    background: var(--brand-red);
    display: flex; align-items: center; justify-content: center;
  }
  .brand-lockup { display: flex; align-items: center; gap: 18px; }
  .brand-lockup__square { width: 46px; height: 46px; background: var(--paper); }
  .brand-lockup__name {
    color: var(--paper); font-weight: 800; font-size: 40px;
    letter-spacing: 2px; text-transform: uppercase;
  }
  /* Back */
  .card--back { background: var(--paper); }
  .card__wave { position: absolute; left: 0; top: 0; width: 700px; height: 400px; }
  .back-brand {
    position: absolute; left: 36px; top: 150px;
    display: flex; align-items: center; gap: 10px;
  }
  .back-brand__square { width: 22px; height: 22px; background: var(--brand-red); flex: none; }
  .back-brand__name {
    color: var(--brand-red); font-weight: 800; font-size: 17px;
    letter-spacing: 0.5px; text-transform: uppercase; white-space: nowrap;
  }
  .divider { position: absolute; left: 288px; top: 60px; width: 60px; height: 170px; }
  .contact { position: absolute; left: 362px; top: 30px; color: var(--ink); }
  .contact__name {
    color: var(--brand-red); font-weight: 800; font-size: 24px;
    letter-spacing: 1px; text-transform: uppercase; line-height: 1.15;
  }
  .contact__title { font-weight: 500; font-size: 14px; margin-bottom: 10px; }
  .contact__address { font-weight: 500; font-size: 13px; line-height: 1.35; margin-bottom: 10px; }
  .contact__list { list-style: none; }
  .contact__item {
    display: flex; align-items: center; gap: 9px;
    font-weight: 500; font-size: 13px; line-height: 1; margin-bottom: 6px;
    white-space: nowrap;
  }
  .contact__icon {
    width: 18px; height: 18px; background: var(--brand-red);
    display: flex; align-items: center; justify-content: center; flex: none;
  }
  .contact__web-accent { color: var(--brand-red); }
</style>
</head>
<body>
<main class="sheet">
  <section class="card card--front">
    <div class="brand-lockup">
      <span class="brand-lockup__square"></span>
      <span class="brand-lockup__name">Veldmark Supplies</span>
    </div>
  </section>

  <section class="card card--back">
    <svg class="card__wave" viewBox="0 0 700 400" aria-hidden="true">
      <path d="M0 372 C 200 364, 360 322, 480 278 C 580 242, 640 238, 700 236 L700 400 L0 400 Z" fill="var(--brand-red)"/>
      <path d="M0 364 C 200 356, 360 314, 480 270 C 580 234, 640 230, 700 228" fill="none" stroke="var(--brand-blue)" stroke-width="4"/>
    </svg>

    <div class="back-brand">
      <span class="back-brand__square"></span>
      <span class="back-brand__name">Veldmark Supplies</span>
    </div>

    <svg class="divider" viewBox="0 0 60 170" aria-hidden="true">
      <line x1="6" y1="0" x2="56" y2="170" stroke="var(--brand-blue)" stroke-width="2"/>
      <line x1="24" y1="24" x2="48" y2="140" stroke="var(--brand-red)" stroke-width="2"/>
      <line x1="4" y1="40" x2="26" y2="160" stroke="var(--brand-red)" stroke-width="2"/>
    </svg>

    <div class="contact">
      <h1 class="contact__name">Dara Whitfield</h1>
      <p class="contact__title">President</p>
      <p class="contact__address">482 Juniper Row, Ste<br>210, Harlow, TX 75990</p>
      <ul class="contact__list">
        <li class="contact__item">
          <span class="contact__icon">
            <svg width="12" height="12" viewBox="0 0 24 24"><path d="M4 9c0-3 16-3 16 0v2h-4V9H8v2H4zM6 12h12l2 8H4z" fill="#fff"/></svg>
          </span>555-214-3706
        </li>
        <li class="contact__item">
          <span class="contact__icon">
            <svg width="12" height="12" viewBox="0 0 24 24"><rect x="7" y="2" width="10" height="20" rx="2" fill="none" stroke="#fff" stroke-width="2"/><circle cx="12" cy="18" r="1.3" fill="#fff"/></svg>
          </span>555-380-1192
        </li>
        <li class="contact__item">
          <span class="contact__icon">
            <svg width="12" height="12" viewBox="0 0 24 24"><rect x="3" y="6" width="18" height="12" fill="none" stroke="#fff" stroke-width="2"/><path d="M3 6l9 7 9-7" fill="none" stroke="#fff" stroke-width="2"/></svg>
          </span>info@veldmarksupplies.com
        </li>
        <li class="contact__item">
          <span class="contact__icon">
            <svg width="12" height="12" viewBox="0 0 24 24"><circle cx="12" cy="12" r="9" fill="none" stroke="#fff" stroke-width="2"/><path d="M3 12h18M12 3c4 4 4 14 0 18M12 3c-4 4-4 14 0 18" fill="none" stroke="#fff" stroke-width="1.5"/></svg>
          </span><span>www.<span class="contact__web-accent">veldmarksupplies</span>.com</span>
        </li>
      </ul>
    </div>
  </section>
</main>
</body>
</html>
```